Business card for Sports Apparel business

DOUBLE SIDED DESIGN
We need business cards for a new sports apparel business. We are developing a protective headband for soccer initially.
Torvalle is focused on designing and developing head protection products to reduce the likelihood of concussion when playing sports. Exploring and understanding medical insights, material science research, current and former players experiences and governing bodies guidelines has allowed Torvalle to develop the safety, style, form and function requirements of a suitable product to bring to market.
Target Market(s)
Mums buying kits for the sons and daughters. Amateur footballers.
Industry/Entity Type
Sporting Good
Contact Information for Business Card
Martin Ashworth - CEO
Mobile: +44 7431589027
Email: martin@torvalle.co.uk
Tel: 0208 5519372
Helena Pargeter - COO
Mob: +44 7385 640117
Email: helena@torvalle.co.uk
Tel: 0208 5519372
Duncan Farrow - CCO
Mob: +44 7564 293081
Email: duncan@torvalle.co.uk
Tel: 0208 5519372
Look and feel
Each slider illustrates characteristics of the customer's brand and the style your logo design should communicate.

```html
<!DOCTYPE html>
<html lang="en">
<head>
<meta charset="utf-8">
<title>Torvalle business card</title>
<link rel="stylesheet" href="https://fonts.googleapis.com/css2?family=Montserrat:wght@500;600;700&family=Roboto:wght@400&display=swap">
<style>
  :root {
    --brand-blue: #0f5d96;
    --brand-blue-dark: #0c5287;
    --ink: #1d1d1d;
    --rule: #b9b9b9;
    --card-white: #ffffff;
    --backdrop: #2b2b2d;
  }
  * { box-sizing: border-box; margin: 0; padding: 0; }
  html, body { width: 1200px; height: 1108px; overflow: hidden; }
  body {
    background: var(--backdrop);
    display: flex;
    align-items: center;
    justify-content: center;
    gap: 60px;
    font-family: "Roboto", Arial, sans-serif;
  }
  .card {
    width: 420px;
    height: 700px;
    border-radius: 30px;
    position: relative;
    overflow: hidden;
  }
  .card-front {
    background: var(--card-white);
    display: flex;
    flex-direction: column;
    align-items: center;
  }
  .wordmark {
    font-family: "Montserrat", Arial, sans-serif;
    font-weight: 600;
    letter-spacing: 0.04em;
    text-transform: uppercase;
  }
  .card-front .wordmark {
    margin-top: 168px;
    font-size: 54px;
    color: var(--brand-blue);
  }
  .holder-name {
    margin-top: 168px;
    font-family: "Montserrat", Arial, sans-serif;
    font-weight: 700;
    font-size: 23px;
    color: var(--brand-blue);
    text-transform: uppercase;
    letter-spacing: 0.01em;
  }
  .holder-role {
    margin-top: 6px;
    font-size: 19px;
    color: var(--ink);
  }
  .contact-divider {
    margin-top: 18px;
    width: 300px;
    display: flex;
    align-items: center;
    gap: 8px;
  }
  .contact-divider::before,
  .contact-divider::after {
    content: "";
    flex: 1;
    height: 1px;
    background: var(--rule);
  }
  .contact-icon {
    width: 26px;
    height: 26px;
    background: var(--brand-blue);
    border-radius: 3px;
    display: flex;
    align-items: center;
    justify-content: center;
  }
  .contact-list {
    margin-top: 14px;
    list-style: none;
    text-align: center;
    font-size: 19px;
    line-height: 1.3;
    color: var(--ink);
  }
  .card-back {
    background: var(--brand-blue);
  }
  .back-pattern {
    position: absolute;
    inset: 0;
    background: linear-gradient(160deg, var(--brand-blue) 0%, var(--brand-blue-dark) 100%);
  }
  .card-back .wordmark {
    position: absolute;
    left: 0;
    right: 0;
    top: 470px;
    text-align: center;
    font-size: 40px;
    color: var(--card-white);
  }
</style>
</head>
<body>
  <section class="card card-front" aria-label="Card front">
    <div class="wordmark">Torvalle</div>
    <h1 class="holder-name">Martin Ashworth</h1>
    <p class="holder-role">CEO</p>
    <div class="contact-divider">
      <span class="contact-icon" aria-label="Telephone">
        <svg width="16" height="16" viewBox="0 0 24 24" fill="#fff"><path d="M6.6 10.8a15 15 0 0 0 6.6 6.6l2.2-2.2a1 1 0 0 1 1-.25 11.4 11.4 0 0 0 3.6.57 1 1 0 0 1 1 1V20a1 1 0 0 1-1 1A17 17 0 0 1 3 4a1 1 0 0 1 1-1h3.5a1 1 0 0 1 1 1c0 1.25.2 2.45.57 3.6a1 1 0 0 1-.25 1z"/></svg>
      </span>
      <span class="contact-icon" aria-label="Mobile">
        <svg width="14" height="16" viewBox="0 0 16 24" fill="none" stroke="#fff" stroke-width="2"><rect x="2" y="1.5" width="12" height="21" rx="2"/><line x1="6" y1="19" x2="10" y2="19"/></svg>
      </span>
      <span class="contact-icon" aria-label="Email">
        <svg width="16" height="12" viewBox="0 0 24 18" fill="none" stroke="#fff" stroke-width="2"><rect x="1.5" y="1.5" width="21" height="15"/><polyline points="1.5,1.5 12,10 22.5,1.5"/></svg>
      </span>
    </div>
    <ul class="contact-list">
      <li>0208 5519372</li>
      <li>+44 7431589027</li>
      <li>martin@torvalle.co.uk</li>
    </ul>
  </section>

  <section class="card card-back" aria-label="Card back">
    <div class="back-pattern" role="img" aria-label="Faint repeated brand name pattern across the blue background"></div>
    <div class="wordmark">Torvalle</div>
  </section>
</body>
</html>
```